wordpress website Carla Winfield, Author, Speaker and Coach

Need a wordpress blogging website for author/speaker/coach.
I have paid for hosting on nestparrot.
I am currently writing a book - Launchpad to Campus - Steps and strategies to prepare you to thrive in college and beyond. Eventually, I will have an Academic/Life Coaching program targeting high school and college students. This website's purpose is to build my email list. I can offer the following reports as incentive for email sign-up:
1. Six Habits That Get Your Teen Through University On Schedule and Debt-Light
2. Surprising Routes to Fund Your Degree
3. SAT/ACT vocabulary word of the day

facebook page: https://www.facebook.com/Carla-Winfield-AcademicLife-Coach-918273645501928/

I would like to have these pages:

1. Home or About page

High school is becoming more and more stressful for students. Not only are they taking more AP classes than ever before, and often spending $1,000’s on SAT/ACT prep programs, most are NOT prepared for success in college. Only 19% of students are graduating from college within 4 years and only 56% are graduating within 6 years. With the cost of higher education skyrocketing, each extra year of school can costs families $40,000 - $60,000 when you factor in living expenses. Then, when students do graduate, they are often underemployed.

Carla's approach is whole person oriented. Her programs help students learn life skills in addition to the study, time management skills, etc. offered by most academic coaching programs. Our program addresses all of the major causes of failure to graduate within 4 years, and is based on sound educational research. Carla's program initially provides the daily interaction needed to successfully change behaviors and seat new success habits, unlike many programs in which students interact with coaches only once a week.
Bio
Carla Winfield is a certified teacher and holds advanced certification in academic coaching and tutoring. She also is a certified trainer in the Morris Tellwright Achievement Keys. She has three successful adult children, and helped them overcome learning differences and thrive.

2. Blog

3. Contact - Include form (I split time between USA and Saudi Arabia, so I will call or email people back, but don't want to leave a phone number)
info@carlawinfield.example

4. Store – 1 book for now
Launchpad to Campus
Steps and strategies to prepare you to thrive in college and beyond
Available 12/01/2017
I could make a preview chapter available for download

5. Speaking
Carla Winfield is available for keynote addresses and half-day, full day or multi-day workshops. I will develop details later

6.Coaching programs
I will develop details later

Target Market(s)

high school students who are college bound and their parents

Number of Pages Required

5+ page

Font styles to use
Sans Serif

Colors

Designer to choose colors to be used in the design.

Requirements
Nice to have
• integration with post finch for contact management

```html
<!DOCTYPE html>
<html lang="en">
<head>
<meta charset="utf-8">
<title>Carla Winfield — Author, Speaker and Coach</title>
<link href="https://fonts.googleapis.com/css2?family=Lato:ital,wght@0,300;0,400;0,700;0,900;1,700&display=swap" rel="stylesheet">
<style>
:root{
  --green:#8cc43f;
  --green-dark:#0b7a42;
  --lavender:#8f8dcb;
  --ink:#2b2b2b;
  --muted:#6b6b6b;
  --light:#f2f2f2;
  --footer:#2a2a2a;
  --footer-bottom:#1b1b1b;
  --white:#ffffff;
}
*{box-sizing:border-box;margin:0;padding:0}
html,body{width:1200px;height:3719px;overflow:hidden}
body{font-family:'Lato',Arial,sans-serif;color:var(--ink);background:var(--white);position:relative}
section,header,footer{position:relative;width:1200px;overflow:hidden}
.abs{position:absolute}
.btn{position:absolute;display:flex;align-items:center;justify-content:center;font-size:13px;font-weight:700;text-transform:uppercase;color:var(--white);letter-spacing:.3px}

/* header */
.site-header{height:69px;background:var(--white);border-bottom:3px solid var(--green)}
.brand{left:160px;top:14px;display:flex;align-items:center;gap:10px}
.brand-dot{width:34px;height:34px;border-radius:50%;background:var(--green)}
.brand-name{font-size:29px;font-weight:700;color:var(--ink)}
.main-nav{left:523px;top:16px;display:flex;align-items:center;font-size:13px}
.nav-home{width:34px;height:36px;background:var(--green);display:flex;align-items:center;justify-content:center;margin-right:12px}
.main-nav a{color:var(--ink);text-decoration:none;padding:0 11px}
.nav-search{width:34px;height:34px;border:1px solid #ccc;display:flex;align-items:center;justify-content:center;margin-left:8px}

/* hero */
.hero{height:476px}
.hero-photo{inset:0;background:linear-gradient(100deg,#8a8580 0%,#b8aea4 35%,#6f6a66 65%,#9c948c 100%)}
.hero-shade{inset:0;background:linear-gradient(90deg,rgba(0,0,0,.35),rgba(0,0,0,.1))}
.hero-arrow{top:200px}
.hero-title{left:155px;top:234px;font-size:31px;font-weight:400;color:var(--white);letter-spacing:1px}
.hero-sub{left:155px;top:283px;font-size:19px;font-weight:700;color:var(--white);line-height:29px}
.btn-buy{left:155px;top:358px;width:144px;height:42px;background:var(--green)}
.btn-contact{left:313px;top:358px;width:139px;height:42px;border:2px solid var(--white)}

/* welcome */
.welcome{height:405px;background:var(--white)}
.welcome-deco{right:-40px;top:10px;width:360px;height:380px;border-radius:50%;background:radial-gradient(circle,#f5f5f5 0%,#ffffff 70%)}
.video-thumb{left:161px;top:64px;width:414px;height:263px;background:linear-gradient(135deg,#3a3330,#7a6e66 50%,#2a2624)}
.video-play{left:182px;top:106px;width:50px;height:50px}
.welcome-title{left:607px;top:78px;font-size:29px;font-weight:400;color:var(--ink)}
.welcome-title strong{font-weight:700}
.welcome-text{left:607px;top:128px;width:440px;font-size:12.5px;line-height:20px;color:#444}
.welcome-text p{margin-bottom:12px}
.btn-read{left:607px;top:300px;width:121px;height:26px;background:var(--lavender);font-size:11px}

/* green band */
.band{height:307px;background:var(--green)}
.band-students{left:136px;top:24px;width:335px;height:283px;background:linear-gradient(180deg,#5c7aa8 0%,#c23b3b 60%,#2a3e66 100%);border-radius:18px 18px 0 0}
.band-title{left:483px;top:66px;font-size:28px;font-weight:700;font-style:italic;color:var(--white)}
.band-text{left:483px;top:118px;width:560px;font-size:12.5px;line-height:19px;font-style:italic;color:var(--white)}
.btn-start{left:483px;top:177px;width:145px;height:38px;background:var(--lavender)}
.btn-shop{left:693px;top:177px;width:127px;height:38px;background:var(--lavender)}

/* programs */
.programs{height:441px;background:linear-gradient(180deg,#f3f3f3,#ececec)}
.section-title{left:0;width:1200px;text-align:center;font-size:30px;font-weight:400;color:var(--ink)}
.programs .section-title{top:52px}
.section-sub{left:0;width:1200px;text-align:center;font-size:12.5px;color:#444}
.programs .section-sub{top:106px}
.program-card{top:154px;width:420px;height:218px;color:var(--white);text-align:center;padding-top:20px}
.card-coaching{left:161px;background:var(--green-dark)}
.card-speaking{left:615px;background:var(--green)}
.program-card svg{display:block;margin:0 auto}
.program-card h3{font-size:24px;font-weight:400;letter-spacing:1px;margin-top:14px}
.program-card p{font-size:12.5px;line-height:17px;margin:6px auto 0;width:340px}
.card-btn{display:inline-flex;align-items:center;gap:6px;background:var(--white);font-size:12px;padding:7px 16px;margin-top:12px}
.card-coaching .card-btn{color:var(--green-dark)}
.card-speaking .card-btn{color:var(--green)}

/* shop */
.shop{height:501px}
.shop-panel{left:0;top:0;width:600px;height:501px;background:var(--lavender)}
.shop-title{left:161px;top:160px;font-size:26px;font-weight:700;color:var(--white)}
.shop-text{left:161px;top:205px;font-size:12.5px;line-height:18px;color:var(--white)}
.btn-view{left:161px;top:296px;width:130px;height:34px;background:var(--green);font-size:12px}
.btn-preview{left:301px;top:296px;width:232px;height:34px;background:var(--green);font-size:12px}
.shop-tile{width:300px;height:250px}
.tile-caption{position:absolute;left:32px;bottom:0;width:236px;height:30px;background:rgba(40,40,40,.85);color:var(--white);font-size:12px;display:flex;align-items:center;justify-content:center}

/* blog */
.blog{height:478px;background:var(--white)}
.blog .section-title{top:20px;font-weight:700;font-size:28px}
.blog-arrow{top:210px}
.post-main{left:174px;top:124px;width:486px;height:268px;background:var(--white);box-shadow:0 0 10px rgba(0,0,0,.12)}
.post-main h4{position:absolute;left:24px;top:20px;width:260px;font-size:18px;font-weight:700;line-height:24px}
.post-meta{position:absolute;left:24px;top:88px;font-size:11px;color:#555}
.post-excerpt{position:absolute;left:24px;top:116px;width:260px;font-size:11.5px;line-height:18px;color:#888}
.post-more{position:absolute;left:24px;top:236px;font-size:11.5px;color:var(--ink)}
.post-thumb-main{left:294px;top:0;width:192px;height:268px;background:linear-gradient(135deg,#c09a70,#6f5b45)}
.date-tag{position:absolute;width:52px;padding:6px 0;background:var(--lavender);color:var(--white);font-size:11px;text-align:center;line-height:15px}
.post-small{left:731px;width:296px;height:122px;background:var(--white);box-shadow:0 0 10px rgba(0,0,0,.12)}
.post-small .thumb{position:absolute;left:0;top:0;width:128px;height:122px}
.post-small h5{position:absolute;left:142px;top:14px;width:140px;font-size:13px;font-weight:400;line-height:17px}
.post-small .ex{position:absolute;left:142px;top:56px;width:140px;font-size:11px;line-height:15px;color:#888}
.post-small .more{position:absolute;left:142px;top:96px;font-size:11px}

/* newsletter */
.newsletter{height:285px;background:var(--green-dark)}
.news-deco{right:60px;top:-40px;width:300px;height:300px;border-radius:50%;background:rgba(255,255,255,.05)}
.newsletter .section-title{top:68px;color:var(--white);font-size:28px}
.newsletter .section-sub{top:122px;color:var(--white);font-style:italic;font-weight:700;font-size:12.5px}
.news-input{left:297px;top:175px;width:395px;height:40px;background:var(--white);font-size:12px;color:#777;padding-left:12px;display:flex;align-items:center}
.btn-subscribe{left:711px;top:175px;width:259px;height:40px;background:var(--green)}

/* testimonials */
.students{height:459px;background:var(--white)}
.students-title{left:161px;top:76px;font-size:29px;font-weight:700}
.students-text{left:161px;top:186px;width:440px;font-size:11.5px;line-height:19px;color:#333}
.students-name{left:161px;top:364px;font-size:17px;font-weight:700;color:var(--green-dark)}
.students-role{left:161px;top:388px;font-size:11px;color:#666}
.students-dots{left:161px;top:408px;display:flex;gap:6px}
.students-dots span{width:24px;height:4px;background:var(--green)}
.students-dots span:first-child{background:var(--green-dark)}
.students-photo{left:640px;top:40px;width:530px;height:419px;background:radial-gradient(ellipse at 50% 60%,#e6b48a 0%,#d96a5e 40%,#ffffff 72%)}

/* footer */
.site-footer{height:253px;background:var(--footer);color:#ddd}
.footer-heading{top:48px;font-size:17px;color:var(--white)}
.quick-links{left:161px;top:90px;list-style:none;font-size:12px;line-height:19px}
.contact-list{left:453px;top:90px;list-style:none;font-size:12px;line-height:17px}
.contact-list li{display:flex;gap:14px;margin-bottom:16px}
.footer-mark{left:820px;top:38px;width:150px;height:150px;border-radius:50%;border:2px solid rgba(255,255,255,.12)}
.footer-bottom{height:45px;background:var(--footer-bottom);color:#ccc;font-size:11px}
.copyright{left:161px;top:15px}
.socials{left:915px;top:12px;display:flex;gap:8px}
.socials span{width:20px;height:20px;background:#555}
</style>
</head>
<body>

<header class="site-header">
  <div class="abs brand"><span class="brand-dot"></span><span class="brand-name">Carla Winfield</span></div>
  <nav class="abs main-nav">
    <span class="nav-home"><svg width="16" height="14" viewBox="0 0 16 14"><path d="M8 1L1 7h2v6h4V9h2v4h4V7h2z" fill="#fff"/></svg></span>
    <a>About Us</a><a>Coaching programs</a><a>Speaking</a><a>Store</a><a>Blog</a><a>Contact Us</a>
    <span class="nav-search"><svg width="12" height="12" viewBox="0 0 12 12"><circle cx="5" cy="5" r="3.6" fill="none" stroke="#444" stroke-width="1.5"/><path d="M7.7 7.7L11 11" stroke="#444" stroke-width="1.5"/></svg></span>
  </nav>
</header>

<section class="hero">
  <div class="abs hero-photo" role="img" aria-label="Photo of students studying together at a table"></div>
  <div class="abs hero-shade"></div>
  <svg class="abs hero-arrow" style="left:108px" width="30" height="62" viewBox="0 0 30 62"><path d="M26 2L4 31l22 29" fill="none" stroke="#fff" stroke-width="3"/></svg>
  <svg class="abs hero-arrow" style="left:1058px" width="30" height="62" viewBox="0 0 30 62"><path d="M4 2l22 29L4 60" fill="none" stroke="#fff" stroke-width="3"/></svg>
  <h1 class="abs hero-title">LEARNING ANY WHERE ANY TIME</h1>
  <p class="abs hero-sub">We Help Students Reach Theri Life Goals Faster<br>And More Efficiently.</p>
  <a class="btn btn-buy">Buy Today !</a>
  <a class="btn btn-contact">Contact Now!</a>
</section>

<section class="welcome">
  <div class="abs welcome-deco"></div>
  <div class="abs video-thumb" role="img" aria-label="Video thumbnail of Carla Winfield speaking">
    <svg class="abs video-play" viewBox="0 0 50 50"><circle cx="25" cy="25" r="25" fill="#fff" opacity=".9"/><path d="M20 15l14 10-14 10z" fill="#333"/></svg>
  </div>
  <h2 class="abs welcome-title">WELCOME TO <strong>CARLA WINFIELD</strong></h2>
  <div class="abs welcome-text">
    <p>Carla Winfield is a certified teacher and holds advanced certification in academic coaching and tutoring. She also is a certified trainer in the Morris Tellwright Achievement Keys. She has three successful adult children, and helped them overcome learning differences and thrive.</p>
    <p>Carla's approach is whole person oriented. Her programs help students learn life skills in addition to the study, time management skills, etc. offered by most academic coaching programs.</p>
  </div>
  <a class="btn btn-read">Read More</a>
</section>

<section class="band">
  <div class="abs band-students" role="img" aria-label="Photo of two smiling students carrying backpacks and books"></div>
  <h2 class="abs band-title">LEARNING WITHOUT LIMITS</h2>
  <p class="abs band-text">It is a long established fact that a reader will be distracted by the readable content of a page when looking at its layout.</p>
  <a class="btn btn-start">Get Start Now</a>
  <a class="btn btn-shop">Shop Now</a>
</section>

<section class="programs">
  <h2 class="abs section-title">OUR PROGRAMS</h2>
  <p class="abs section-sub">Lorem Ipsum is simply dummy text of the printing and typesetting industry. Lorem Ipsum has been the industry's</p>
  <div class="abs program-card card-coaching">
    <svg width="40" height="36" viewBox="0 0 40 36"><circle cx="14" cy="9" r="6" fill="#fff"/><circle cx="27" cy="12" r="5" fill="#fff"/><path d="M3 30c0-7 5-12 11-12s11 5 11 12z" fill="#fff"/><path d="M22 30c1-6 3-9 6-9 5 0 9 4 9 9z" fill="#fff"/></svg>
    <h3>COACHING PROGRAMS</h3>
    <p>Lorem Ipsum is simply dummy text of the printing and typesetting industry. Lorem Ipsum has been the industry's</p>
    <span class="card-btn">Read More <svg width="8" height="8" viewBox="0 0 8 8"><path d="M2 1l4 3-4 3" fill="none" stroke="currentColor" stroke-width="1.6"/></svg></span>
  </div>
  <div class="abs program-card card-speaking">
    <svg width="40" height="36" viewBox="0 0 40 36"><rect x="16" y="2" width="20" height="13" rx="2" fill="none" stroke="#fff" stroke-width="2"/><circle cx="12" cy="14" r="5" fill="#fff"/><path d="M2 34c0-7 4-12 10-12s10 5 10 12z" fill="#fff"/></svg>
    <h3>SPEAKING PROGRAMS</h3>
    <p>Lorem Ipsum is simply dummy text of the printing and typesetting industry. Lorem Ipsum has been the industry's</p>
    <span class="card-btn">Read More <svg width="8" height="8" viewBox="0 0 8 8"><path d="M2 1l4 3-4 3" fill="none" stroke="currentColor" stroke-width="1.6"/></svg></span>
  </div>
</section>

<section class="shop">
  <div class="abs shop-panel"></div>
  <h2 class="abs shop-title">SHOP</h2>
  <p class="abs shop-text">Launchpad to Campus<br>Steps and strategies to prepare you to thrive in college and beyond<br>Available 12/01/2017</p>
  <a class="btn btn-view">View Shop</a>
  <a class="btn btn-preview">Download Preview Chapter</a>
  <div class="abs shop-tile" style="left:600px;top:0;background:linear-gradient(135deg,#a6553d,#d8c1b0)" role="img" aria-label="Photo of a student holding books by a brick wall"><span class="tile-caption">1 Chapter Available</span></div>
  <div class="abs shop-tile" style="left:900px;top:0;background:linear-gradient(135deg,#6f8f4a,#caa98a)" role="img" aria-label="Photo of a student outdoors with a notebook"><span class="tile-caption">2 Chapter Available</span></div>
  <div class="abs shop-tile" style="left:600px;top:250px;background:linear-gradient(135deg,#d94e6a,#f0c08f)" role="img" aria-label="Photo of a cheerful group of students"><span class="tile-caption">3 Chapter Available</span></div>
  <div class="abs shop-tile" style="left:900px;top:250px;background:linear-gradient(135deg,#d8d2c8,#8a7868)" role="img" aria-label="Photo of students studying at a desk"><span class="tile-caption">4 Chapter Available</span></div>
</section>

<section class="blog">
  <h2 class="abs section-title">LETEST BLOG</h2>
  <svg class="abs blog-arrow" style="left:116px" width="18" height="34" viewBox="0 0 18 34"><path d="M15 2L3 17l12 15" fill="none" stroke="#888" stroke-width="3"/></svg>
  <svg class="abs blog-arrow" style="left:1063px" width="18" height="34" viewBox="0 0 18 34"><path d="M3 2l12 15L3 32" fill="none" stroke="#888" stroke-width="3"/></svg>
  <article class="abs post-main">
    <h4>Lorem ipsum dolor sit amet, consectetuer</h4>
    <span class="post-meta">Posted by : Admin</span>
    <p class="post-excerpt">Since moving to digital photos years back, I have developed a happy finger when it comes to taking pictures, so going thru all the pictures that I Lorem ipsum dolor sit amet, consectetuer adipiscing elit, sed diam nonummy nibh.</p>
    <span class="post-more">Read More →</span>
    <div class="abs post-thumb-main" role="img" aria-label="Photo of a hand writing in a notebook"></div>
    <span class="date-tag" style="left:294px;top:0">30 JUN<br>2017</span>
  </article>
  <article class="abs post-small" style="top:124px">
    <div class="thumb" role="img" aria-label="Photo of students in a classroom" style="background:linear-gradient(135deg,#7a6aa0,#d9a070)"></div>
    <span class="date-tag" style="left:0;top:0">29 Jun<br>2017</span>
    <h5>Lorem ipsum dolor sit amet, consectetuer</h5>
    <p class="ex">Since moving to digital photos years back...</p>
    <span class="more">Read More →</span>
  </article>
  <article class="abs post-small" style="top:268px">
    <div class="thumb" role="img" aria-label="Photo of a teacher speaking to a class" style="background:linear-gradient(135deg,#c9bfb6,#7a5a66)"></div>
    <span class="date-tag" style="left:0;top:0">28 Jun<br>2017</span>
    <h5>Lorem ipsum dolor sit amet, consectetuer</h5>
    <p class="ex">Since moving to digital photos years back...</p>
    <span class="more">Read More →</span>
  </article>
</section>

<section class="newsletter">
  <div class="abs news-deco"></div>
  <h2 class="abs section-title">Subscribe To Our Newsletter</h2>
  <p class="abs section-sub">Sign Up To Receive Email Updates About Courses</p>
  <div class="abs news-input">Enter your email</div>
  <a class="btn btn-subscribe">Subscribe</a>
</section>

<section class="students">
  <h2 class="abs students-title">OUR HAPPY STUDENTS</h2>
  <p class="abs students-text">Lorem Ipsum is simply dummy text of the printing and typesetting industry. Lorem Ipsum has been the industry's standard dummy text ever since the 1500s, when an unknown printer took a galley of type and scrambled it to make a type specimen book. It has survived not only five centuries, but also the leap into electronic typesetting, remaining essentially unchanged. It was popularised in the 1960s with the release of Lettrafold sheets containing Lorem Ipsum passages, and more recently with desktop publishing software like Quillmark PageSetter including versions of Lorem Ipsum.</p>
  <span class="abs students-name">Mr Lorem Lpsum</span>
  <span class="abs students-role">Creative Manager</span>
  <div class="abs students-dots"><span></span><span></span><span></span></div>
  <div class="abs students-photo" role="img" aria-label="Photo of a group of students jumping and cheering"></div>
</section>

<footer class="site-footer">
  <h3 class="abs footer-heading" style="left:161px">Quick Links</h3>
  <ul class="abs quick-links"><li>Home</li><li>About Us</li><li>Coaching programs</li><li>Speaking</li><li>Store</li><li>Blog</li><li>Contact Us</li></ul>
  <h3 class="abs footer-heading" style="left:453px">Contact Us</h3>
  <ul class="abs contact-list">
    <li><svg width="10" height="14" viewBox="0 0 10 14"><path d="M5 0a5 5 0 0 1 5 5c0 4-5 9-5 9S0 9 0 5a5 5 0 0 1 5-5z" fill="#999"/><circle cx="5" cy="5" r="1.8" fill="#2a2a2a"/></svg><span>CARLAWINFIELD<br>lorem lpsum dolor lpsum volt<br>amet dolor - 123456</span></li>
    <li><svg width="12" height="12" viewBox="0 0 12 12"><path d="M2 0l3 3-1.5 1.5a7 7 0 0 0 4 4L9 7l3 3-2 2C5 12 0 7 0 2z" fill="#999"/></svg><span>(65) 4210 7786</span></li>
    <li><svg width="13" height="10" viewBox="0 0 13 10"><rect width="13" height="10" fill="none" stroke="#999" stroke-width="1.4"/><path d="M0 0l6.5 5L13 0" fill="none" stroke="#999" stroke-width="1.4"/></svg><span>info@carlawinfield.example</span></li>
  </ul>
  <div class="abs footer-mark"></div>
</footer>
<footer class="footer-bottom">
  <span class="abs copyright">Copyright © CARLAWINFIELD All Rights Reserved</span>
  <div class="abs socials"><span></span><span></span><span></span><span></span></div>
</footer>

</body>
</html>
```